Meadow Kr Circle (company name is Meadow Kr Circle LLP)

management of homestay, hospitality something similar with https://www.dorvika.example

Target Market(s)

johor bahru market (Malaysia)

Contact Information for Business Card

Meadow Circle KR LLP

Logo Text

eyes catching, attractive, amazing, Nice, jaw dropping for design

Coding

Coded - Design and coding required

Number of Pages Required

5+ page

Colors

Designer to choose colors to be used in the design.

Requirements
Must have
• please change the short term proposal to our company logo and change the name from dorvika to meadow KR Circle LLP
• thanks
Nice to have
• please let me have eyes catching , jaw dropping design

```html
<!DOCTYPE html>
<html lang="en">
<head>
<meta charset="utf-8">
<title>Meadow KR Circle – Business Cards</title>
<link rel="stylesheet" href="https://fonts.googleapis.com/css2?family=Nunito+Sans:wght@700;800&display=swap">
<style>
  :root {
    --sheet: #dcdcdc;
    --white: #ffffff;
    --purple: #4a0a6e;
    --purple-deep: #3d0766;
    --orange: #e2620e;
    --orange-warm: #c8550a;
    --red: #a8000e;
    --red-warm: #c42a10;
    --red-dark: #8a0a0a;
    --bracket: #d9573a;
    --sky: #1a9ad6;
    --navy: #0a0a9a;
    --navy-ink: #1a1a8a;
    --name-box: #1a2fa0;
    --cream: #f6f3ee;
  }
  * { margin: 0; padding: 0; box-sizing: border-box; }
  html, body { width: 895px; height: 1200px; overflow: hidden; }
  body {
    background: var(--sheet);
    font-family: "Nunito Sans", Arial, sans-serif;
    font-weight: 800;
    position: relative;
  }
  .card {
    position: absolute;
    width: 386px;
    height: 220px;
    overflow: hidden;
  }
  .card svg.bg { position: absolute; inset: 0; width: 100%; height: 100%; }
  .col-front { left: 53px; }
  .col-back { left: 459px; }
  .row-1 { top: 98px; }
  .row-2 { top: 362px; }
  .row-3 { top: 631px; }
  .row-4 { top: 895px; }

  .brand {
    position: absolute;
    display: flex;
    flex-direction: column;
    align-items: center;
    text-align: center;
    transform: translateX(-50%);
  }
  .brand-dot {
    width: 46px; height: 46px;
    border-radius: 50%;
    border: 3px solid currentColor;
    margin-bottom: 8px;
  }
  .brand-name { line-height: 1.05; letter-spacing: 0.2px; }

  .holder {
    position: absolute;
    color: var(--white);
    text-transform: uppercase;
  }
  .holder-name { font-size: 19px; line-height: 0.95; }
  .holder-address { font-size: 10.5px; font-weight: 700; line-height: 1.25; margin-top: 8px; }
  .pattern-fill { position: absolute; inset: 0; background: var(--cream); }
</style>
</head>
<body>

<!-- Sunset front -->
<section class="card col-front row-1">
  <svg class="bg" viewBox="0 0 386 220">
    <defs>
      <linearGradient id="sunset" x1="0" y1="0" x2="0.7" y2="1">
        <stop offset="0" stop-color="var(--orange-warm)"/>
        <stop offset="0.65" stop-color="var(--purple)"/>
        <stop offset="1" stop-color="var(--purple-deep)"/>
      </linearGradient>
    </defs>
    <rect width="386" height="220" fill="url(#sunset)"/>
  </svg>
  <div class="brand" style="left:197px; top:62px; color:var(--white);">
    <span class="brand-dot"></span>
    <span class="brand-name" style="font-size:19px;">MEADOW KR CIRCLE</span>
  </div>
</section>

<!-- Sunset back -->
<section class="card col-back row-1">
  <svg class="bg" viewBox="0 0 386 220">
    <rect width="386" height="220" fill="var(--white)"/>
    <polygon points="241,0 256,0 176,86 295,220 280,220 164,90" fill="var(--orange)"/>
    <polygon points="254,0 386,0 386,220 293,220 176,86" fill="var(--purple)"/>
  </svg>
  <div class="brand" style="left:97px; top:72px; color:var(--purple);">
    <span class="brand-dot" style="width:36px;height:36px;color:var(--orange);"></span>
    <span class="brand-name" style="font-size:15px;">MEADOW KR CIRCLE</span>
  </div>
  <div class="holder" style="left:245px; top:47px;">
    <div class="holder-name">Aria<br>Tan Wei</div>
    <div class="holder-address">L12-04 Harbour Crest,<br>Jalan Seruni,<br>Taman Pelangi,<br>80400 Johor Bahru.</div>
  </div>
</section>

<!-- Red front -->
<section class="card col-front row-2">
  <svg class="bg" viewBox="0 0 386 220">
    <defs>
      <linearGradient id="crimson" x1="0" y1="0" x2="0" y2="1">
        <stop offset="0" stop-color="var(--red)"/>
        <stop offset="1" stop-color="var(--red-warm)"/>
      </linearGradient>
    </defs>
    <rect width="386" height="220" fill="url(#crimson)"/>
    <g fill="none" stroke="var(--bracket)" stroke-width="2.5">
      <polyline points="38,78 38,26 150,26"/>
      <polyline points="239,26 351,26 351,78"/>
      <polyline points="38,136 38,192 150,192"/>
      <polyline points="239,192 351,192 351,136"/>
    </g>
  </svg>
  <div class="brand" style="left:196px; top:56px; color:var(--white);">
    <span class="brand-dot"></span>
    <span class="brand-name" style="font-size:22px;">MEADOW KR CIRCLE</span>
  </div>
</section>

<!-- Red back -->
<section class="card col-back row-2">
  <svg class="bg" viewBox="0 0 386 220">
    <defs>
      <linearGradient id="crimson-b" x1="0" y1="0" x2="0" y2="1">
        <stop offset="0" stop-color="var(--red)"/>
        <stop offset="1" stop-color="var(--red-warm)"/>
      </linearGradient>
    </defs>
    <rect width="386" height="220" fill="url(#crimson-b)"/>
    <path d="M0,0 H156 Q222,110 152,220 H0 Z" fill="var(--red-dark)"/>
    <path d="M0,0 H146 Q210,110 142,220 H0 Z" fill="var(--white)"/>
  </svg>
  <div class="brand" style="left:100px; top:60px; color:var(--red);">
    <span class="brand-dot" style="width:38px;height:38px;"></span>
    <span class="brand-name" style="font-size:17px;">MEADOW KR<br>CIRCLE</span>
  </div>
  <div class="holder" style="left:281px; top:54px; transform:translateX(-50%); text-align:center;">
    <div class="holder-name">Aria<br>Tan Wei</div>
    <div class="holder-address">L12-04 Harbour Crest,<br>Jalan Seruni,<br>Taman Pelangi,<br>80400 Johor Bahru.</div>
  </div>
</section>

<!-- Ocean front -->
<section class="card col-front row-3">
  <svg class="bg" viewBox="0 0 386 220">
    <defs>
      <linearGradient id="ocean" x1="0" y1="0" x2="0" y2="1">
        <stop offset="0" stop-color="var(--sky)"/>
        <stop offset="1" stop-color="var(--navy)"/>
      </linearGradient>
    </defs>
    <rect width="386" height="220" fill="url(#ocean)"/>
    <path d="M0,122 Q60,104 130,124 T260,120 T386,114 V220 H0 Z" fill="#1560c8" opacity="0.55"/>
    <path d="M0,150 Q80,132 160,152 T320,146 T386,150 V220 H0 Z" fill="#0e3fb0" opacity="0.6"/>
    <path d="M0,182 Q70,166 150,184 T300,178 T386,184 V220 H0 Z" fill="#08209a" opacity="0.7"/>
    <path d="M0,206 Q90,194 180,208 T386,204 V220 H0 Z" fill="#060e80" opacity="0.8"/>
  </svg>
  <div class="brand" style="left:200px; top:50px; color:var(--white);">
    <span class="brand-dot"></span>
    <span class="brand-name" style="font-size:22px;">MEADOW KR CIRCLE</span>
  </div>
</section>

<!-- Ocean back -->
<section class="card col-back row-3">
  <svg class="bg" viewBox="0 0 386 220">
    <defs>
      <linearGradient id="ocean-b" x1="0" y1="0" x2="0" y2="1">
        <stop offset="0" stop-color="var(--sky)"/>
        <stop offset="1" stop-color="var(--navy)"/>
      </linearGradient>
    </defs>
    <rect width="386" height="220" fill="url(#ocean-b)"/>
    <path d="M0,0 H180 Q186,170 30,220 H0 Z" fill="#6a6ab8"/>
    <path d="M0,0 H176 Q176,160 28,220 H0 Z" fill="var(--white)"/>
    <rect x="196" y="37" width="190" height="58" fill="var(--name-box)"/>
  </svg>
  <div class="brand" style="left:84px; top:30px; color:var(--navy-ink);">
    <span class="brand-dot" style="width:38px;height:38px;color:var(--sky);"></span>
    <span class="brand-name" style="font-size:17px;">MEADOW KR<br>CIRCLE</span>
  </div>
  <div class="holder" style="left:209px; top:44px;">
    <div class="holder-name" style="font-size:23px;">Aria<br>Tan Wei</div>
    <div class="holder-address" style="font-size:12.5px; margin-top:20px;">L12-04 Harbour Crest,<br>Jalan Seruni,<br>Taman Pelangi,<br>80400 Johor Bahru.</div>
  </div>
</section>

<!-- Pattern front -->
<section class="card col-front row-4">
  <div class="pattern-fill" role="img" aria-label="Light geometric line pattern background"></div>
  <div class="brand" style="left:202px; top:62px; color:var(--purple);">
    <span class="brand-dot" style="color:var(--orange);"></span>
    <span class="brand-name" style="font-size:20px;">MEADOW KR CIRCLE</span>
  </div>
</section>

<!-- Pattern back -->
<section class="card col-back row-4">
  <div class="pattern-fill" role="img" aria-label="Light geometric line pattern background"></div>
  <svg class="bg" viewBox="0 0 386 220">
    <defs>
      <linearGradient id="dusk" x1="0" y1="0" x2="0" y2="1">
        <stop offset="0" stop-color="var(--purple)"/>
        <stop offset="0.55" stop-color="#a0282e"/>
        <stop offset="1" stop-color="var(--orange)"/>
      </linearGradient>
    </defs>
    <polygon points="265,0 333,90 282,220" fill="var(--red-dark)"/>
    <polygon points="130,0 64,126 130,220" fill="var(--red-dark)"/>
    <polygon points="136,0 260,0 325,92 278,220 136,220 72,126" fill="url(#dusk)"/>
    <line x1="120" y1="98" x2="290" y2="98" stroke="#ffffff" stroke-opacity="0.3" stroke-width="1"/>
  </svg>
  <div class="brand" style="left:206px; top:28px; color:var(--white);">
    <span class="brand-dot" style="width:30px;height:30px;margin-bottom:6px;"></span>
    <span class="brand-name" style="font-size:14px;">MEADOW KR CIRCLE</span>
  </div>
  <div class="holder" style="left:203px; top:117px; transform:translateX(-50%); text-align:center; white-space:nowrap;">
    <div class="holder-name" style="font-size:16px;">Aria Tan Wei</div>
    <div class="holder-address" style="font-size:9px; margin-top:9px;">L12-04 Harbour Crest,<br>Jalan Seruni, Taman Pelangi,<br>80400 Johor Bahru.</div>
  </div>
</section>

</body>
</html>
```